Angebotsflyer Velia Cosmetics
Zielgruppe
Kosmetikstudio, Einzelfirma Inhabergeführt
Klientel: Damen 30+ jährig
Naturkosmetik, keine apparative Kosmetik
Aufgabenstellung
Logo und Flyer (Eröffnung) im Anhang wurden bereits über Flinkwerk.de gestaltet. Aus unserer Sicht schöne Vorlage.
Geforderter Leistungsumfang:
1. Flyer 3-seitig, DIN Lang (Hochformat). Angebotsflyer Velia Cosmetics. Idee gemäss Anhang, Aussenseiten schwarz, Innenseiten weiss (bessere Lesbarkeit). TEXT gemäss Anhang.
2. Flyer 1-seitig, DIN Lang (Hochformat). Kunden werben für Kunden. Dieser Flyer kann dem Angebotsflyer als Einlage mitgegeben werden und soll natürlich dem ähnlichen Stil des Angebotsflyers entsprechen. Ideen gemäss Anhang. Keine TEXT-Vorgabe im Anhang, kann durch Designer gestaltet werden. Als Prämie werden 15 CHF + 15 CHF auf die nächste Gesichtsbehandlung vergütet.

```html
<!DOCTYPE html>
<html lang="de">
<head>
<meta charset="utf-8">
<title>Angebotsflyer Velia Cosmetics – Innenseiten</title>
<link href="https://fonts.googleapis.com/css2?family=Montserrat:wght@300;400;500&display=swap" rel="stylesheet">
<style>
  :root{
    --gold:#c08f55;
    --ink:#2b2b2b;
    --paper:#f7f6f4;
    --night:#121212;
    --night-text:#e6e6e6;
    --stage:#e9e7e3;
    --fold:#e2e0dc;
  }
  *{box-sizing:border-box;margin:0;padding:0}
  html,body{width:1200px;height:970px;overflow:hidden}
  body{background:var(--stage);font-family:'Montserrat',sans-serif;color:var(--ink)}

  .flyer{position:absolute;left:15px;top:35px;width:1170px;height:900px;display:flex}
  .panel{position:relative;width:390px;height:900px;overflow:hidden}
  .panel--light{background:var(--paper)}
  .panel--light + .panel--light{border-left:1px solid var(--fold)}
  .panel--dark{background:var(--night);color:var(--night-text)}

  .hero{position:absolute;left:0;top:0;width:390px;height:265px}
  .hero__band{position:absolute;left:0;top:0;width:390px;height:265px}
  .block{position:absolute;left:33px;right:22px}

  .title{font-weight:300;color:var(--gold);font-size:25px;line-height:30px;letter-spacing:.3px}
  .heading{font-weight:300;color:var(--gold);font-size:17px;line-height:21px}
  .lead{font-size:13px;line-height:20px}
  .text{font-size:12.5px;line-height:21px}

  .service{display:flex;align-items:center;gap:26px}
  .service__img{width:80px;height:80px;border-radius:50%;border:1.5px solid var(--gold);flex:none}

  .ticks{list-style:none;font-size:12.5px;line-height:21px}
  .ticks li{position:relative;padding-left:20px;margin-bottom:5px}
  .ticks li svg{position:absolute;left:0;top:5px;width:12px;height:10px}

  .gift{position:absolute;left:0;top:779px;width:68px;height:96px;background:linear-gradient(180deg,#2a2a2a,#0d0d0d)}

  .dark-block{position:absolute;left:30px;right:22px}
  .brand{font-size:12px;letter-spacing:3px;font-weight:500;color:#fff;display:flex;align-items:center;gap:8px;line-height:16px}
  .brand__dot{width:10px;height:10px;background:var(--gold);border-radius:50%}
  .brand--plain{letter-spacing:1px;font-weight:400}
  .dark-heading{font-size:13px;line-height:18px;color:var(--gold);font-weight:400}
  .dark-text{font-size:11px;line-height:19.5px}
</style>
</head>
<body>
<svg width="0" height="0" style="position:absolute">
  <defs>
    <symbol id="tick" viewBox="0 0 12 10"><path d="M1 5.5 L4.3 8.6 L11 1.2" fill="none" stroke="#c08f55" stroke-width="1.4"/></symbol>
    <linearGradient id="goldBand" x1="0" y1="0" x2="1" y2="0">
      <stop offset="0" stop-color="#e6c88f"/><stop offset=".5" stop-color="#d1a868"/><stop offset="1" stop-color="#b5833f"/>
    </linearGradient>
  </defs>
</svg>

<main class="flyer">
  <!-- Panel 1: Behandlungen -->
  <section class="panel panel--light">
    <div class="hero" role="img" aria-label="Foto: Gesichtsmaske wird mit Pinsel aufgetragen" style="background:linear-gradient(120deg,#f2ece7,#e7dcd4 55%,#d9c8bd)"></div>
    <svg class="hero__band" viewBox="0 0 390 265">
      <polygon points="0,166 390,250 390,258 0,212" fill="url(#goldBand)"/>
      <polygon points="0,212 390,258 390,265 0,265" fill="#f7f6f4"/>
    </svg>

    <h1 class="block title" style="top:253px">Behandlungen</h1>
    <p class="block lead" style="top:306px">Folgende Behandlungen biete ich Ihnen gerne an:</p>

    <div class="block service" style="top:355px">
      <div class="service__img" role="img" aria-label="Porträtfoto einer Frau bei der Gesichtspflege" style="background:radial-gradient(circle,#e8cbb4,#c9a98f)"></div>
      <h2 class="heading">Gesichtspflege<br>by AMAVEDA</h2>
    </div>

    <ul class="block ticks" style="top:463px">
      <li><svg><use href="#tick"/></svg>Wohlfühlgesichtsbehandlung –<br>mit speziellem Fussritual</li>
      <li><svg><use href="#tick"/></svg>Klassische Gesichtsbehandlung –<br>perfekt auf Ihren Hauttyp abgestimmt</li>
      <li><svg><use href="#tick"/></svg>Straffende Anti-Aging Gesichtsbehandlung</li>
      <li><svg><use href="#tick"/></svg>Kurze Gesichtsbehandlung</li>
      <li><svg><use href="#tick"/></svg>Gentleman’s Corner – einfach entspannen!</li>
    </ul>

    <div class="block service" style="top:656px">
      <div class="service__img" role="img" aria-label="Nahaufnahme eines geschminkten Auges mit Augenbraue" style="background:radial-gradient(circle,#d9a67c,#a86f48)"></div>
      <h2 class="heading">Wimpern- und<br>Augenbrauen färben</h2>
    </div>

    <p class="block text" style="top:764px">Ein Muss für geheimnisvolle, elegant verführerische Blicke. Die dunkeln Wimpern sowie farblich abgestimmten Augenbrauen und Formen verleihen Ihrem Gesicht mehr Ausdruck. Wenig Aufwand – grosser Effekt.</p>
  </section>

  <!-- Panel 2: Make-up, Epilation, Gutschein -->
  <section class="panel panel--light">
    <div class="hero" role="img" aria-label="Foto: Lidschattenpalette in Violett- und Rosétönen" style="background:linear-gradient(110deg,#5d5566,#8a7d8c 45%,#b9a6a6 75%,#d4c4bd)"></div>
    <svg class="hero__band" viewBox="0 0 390 265">
      <polygon points="0,180 390,240 390,255 0,222" fill="url(#goldBand)"/>
      <polygon points="0,222 390,255 390,265 0,265" fill="#f7f6f4"/>
    </svg>

    <div class="block service" style="top:258px;left:30px">
      <div class="service__img" role="img" aria-label="Make-up-Pinsel mit violettem Puder" style="background:radial-gradient(circle at 40% 40%,#c6a3d1,#f5f2f4 70%)"></div>
      <h2 class="heading">Make-up</h2>
    </div>
    <p class="block text" style="top:362px;left:30px">Natürlich, dezent, raffiniert oder gewagt?<br>Für jeden Anlass das passende Make-up.</p>
    <ul class="block ticks" style="top:425px;left:30px">
      <li><svg><use href="#tick"/></svg>Tages Make-up</li>
      <li><svg><use href="#tick"/></svg>Familenfest, Abend-/ oder Hochzeitsmake-up</li>
    </ul>

    <div class="block service" style="top:499px;left:30px">
      <div class="service__img" role="img" aria-label="Foto glatter Frauenbeine" style="background:radial-gradient(circle,#e7b592,#f6f1ee 75%)"></div>
      <h2 class="heading">Epilation<br>mit Silkora Sugaring</h2>
    </div>
    <p class="block text" style="top:609px;left:30px">Professionelle, natürlich schonende Haarentfernung .</p>
    <ul class="block ticks" style="top:650px;left:30px">
      <li><svg><use href="#tick"/></svg>Gesicht/Oberlippe/Kinn</li>
      <li><svg><use href="#tick"/></svg>Körper/Beine/Achselhöhlen/Bikini</li>
      <li><svg><use href="#tick"/></svg>In Kombinationen mit Preisvorteil</li>
    </ul>

    <div class="gift" role="img" aria-label="Schwarze Geschenkschachtel mit goldener Schleife"></div>
    <h2 class="block heading" style="top:757px;left:84px">Geschenkgutschein</h2>
    <p class="block text" style="top:800px;left:84px;right:14px">Sie wollen eine besondere Freude machen? Ich habe eine Auswahl an liebevoll kreierten, handgefertigten Geschenkkarten.</p>
  </section>

  <!-- Panel 3: Marken -->
  <section class="panel panel--dark">
    <p class="dark-block dark-text" style="top:50px">Mit viel Freude und Ueberzeugung sowie Wertschätzung auf unsere Natur arbeite ich mit spezialisierten Marken und ihren grossen Produktepaletten.</p>

    <p class="dark-block brand" style="top:163px"><span class="brand__dot"></span>AMAVEDA</p>
    <h3 class="dark-block dark-heading" style="top:198px">AMAVEDA - natürliche Kosmetikprodukte</h3>
    <p class="dark-block dark-text" style="top:234px">AMAVEDA Produkte sind überwiegend aus organischen Inhaltsstoffen formuliert und enthalten keine synthetische Duft- oder Farbstoffe. Die verwendeten ätherische Oele besitzen therapeutische Güte. Die ayurvedische Produktepalette von AMAVEDA lässt für jeden Hauttyp und Bedürfnis das Richtige finden und trägt dazu bei, dass Körper, Geist und Seele im Einklang sind.</p>

    <p class="dark-block brand brand--plain" style="top:425px">lindhorst</p>
    <h3 class="dark-block dark-heading" style="top:474px">Lindhorst Cosmetics – ganz natürlich</h3>
    <p class="dark-block dark-text" style="top:512px">Natürliche Inhaltsstoffe – höchste Qualität. Die hochwertigen Make-up Produkte der Lindhorst Cosmetics lässt Sie strahlen. Sie sind biologisch, vegan, ohne Parabene und glutenfrei. Für jeden Teint findet sich die optimale Farbe und lässt Ihre Haut ebenmässig und natürlich aussehen. Ueberzeugen Sie sich selbst!</p>

    <p class="dark-block brand brand--plain" style="top:660px;font-size:15px;line-height:18px">silkora</p>
    <h3 class="dark-block dark-heading" style="top:709px">Silkora – schonende, effektive Haarentfernung</h3>
    <p class="dark-block dark-text" style="top:746px">Die natürliche Haarentfernung auch Body-Sugaring genannt, ist eine sanfte und langanhaltende Alternative zum Rasieren oder Wachsen. Silkora ist 100% natürlich, wasserlöslich und ohne Zusatz von Konservierungsstoffen. Ihre Haare wachsen feiner und langsamer nach – für ein rundum zartes Hautgefühl!</p>
  </section>
</main>
</body>
</html>
```